Maple Roster Business Card for recruitment company

We are looking for a Business Card Design that incorporates our personal details and our busines name and logo. We are a specialized search consultancy that recruit Property and Construction professionals.
We would like a business card that stands out and is appealing to the Construction and Property industry as well.

Target Market(s)

people in the construction and property industry

Contact Information for Business Card

Business Name and logo

Font styles to use
Serif

Colors
0094D4
00A9DD
6FCCEA
C7EBF8
E9F6FB

Requirements
Must have
• Business name and logo as well as contact details
Should not have
• No photos of us please

```html
<!DOCTYPE html>
<html lang="en">
<head>
<meta charset="utf-8">
<title>Maple Roster — Business Card</title>
<link rel="stylesheet" href="https://fonts.googleapis.com/css2?family=Jost:wght@300;400&family=Arimo:wght@400&display=swap">
<style>
  :root {
    --backdrop: #8e8e8e;
    --paper: #ffffff;
    --ink-brand: #033a4f;
    --ink-text: #111111;
    --card-shadow: #1a1a1a;
  }
  * { margin: 0; padding: 0; box-sizing: border-box; }
  html, body { width: 1075px; height: 1200px; overflow: hidden; }
  body { background: var(--backdrop); position: relative; font-family: "Arimo", Arial, sans-serif; }

  .card { position: absolute; width: 663px; height: 395px; box-shadow: 3px 3px 2px var(--card-shadow); }
  .card-front { left: 206px; top: 187px; background: var(--paper); }
  .card-back { left: 203px; top: 637px; height: 396px; background: var(--ink-brand); overflow: hidden; }

  .holder { position: absolute; left: 35px; top: 50px; }
  .holder-name { font-family: "Jost", sans-serif; font-weight: 400; font-size: 29px; color: var(--ink-brand); line-height: 1; letter-spacing: 0.2px; }
  .holder-role { font-size: 17px; color: var(--ink-text); margin-top: 2px; }

  .wordmark { position: absolute; font-family: "Jost", sans-serif; font-weight: 300; color: var(--ink-brand); white-space: nowrap; line-height: 1; }
  .card-front .wordmark { right: 40px; top: 158px; font-size: 46px; letter-spacing: 0.5px; }

  .contact { position: absolute; left: 35px; top: 252px; font-size: 18px; color: var(--ink-text); line-height: 24px; }
  .contact-line { display: flex; align-items: center; gap: 5px; }
  .contact-line svg { width: 19px; height: 17px; fill: var(--ink-brand); }
  .address { margin-top: 10px; line-height: 24px; }

  .website { position: absolute; right: 41px; top: 331px; font-size: 18px; color: var(--ink-text); }
  .website span { color: var(--ink-brand); }

  .accent-bar { position: absolute; left: 416px; bottom: 0; width: 204px; height: 12px; background: var(--ink-brand); }

  .back-pattern { position: absolute; inset: 0; background: linear-gradient(135deg, #063f55, #033a4f 60%, #04394d); }
  .card-back .wordmark { left: 430px; top: 276px; font-size: 29px; font-weight: 400; color: var(--paper); }
</style>
</head>
<body>

<section class="card card-front" aria-label="Card front">
  <div class="holder">
    <p class="holder-name">DANIEL HARPER</p>
    <p class="holder-role">Managing Director</p>
  </div>

  <p class="wordmark">MAPLE ROSTER</p>

  <div class="contact">
    <p class="contact-line">
      <svg viewBox="0 0 24 24" aria-hidden="true"><path d="M6.6 10.8a15.1 15.1 0 0 0 6.6 6.6l2.2-2.2c.3-.3.7-.4 1-.2 1.1.4 2.3.6 3.6.6.6 0 1 .4 1 1V20c0 .6-.4 1-1 1A17 17 0 0 1 3 4c0-.6.4-1 1-1h3.5c.6 0 1 .4 1 1 0 1.3.2 2.5.6 3.6.1.3 0 .7-.2 1z"/><path d="M14 3a7 7 0 0 1 7 7h-1.8A5.2 5.2 0 0 0 14 4.8zm0 3.5a3.5 3.5 0 0 1 3.5 3.5h-1.8A1.7 1.7 0 0 0 14 8.3z"/></svg>
      044-555 210 347
    </p>
    <p class="contact-line">
      <svg viewBox="0 0 24 18" aria-hidden="true"><path d="M0 1h24v16H0z" /><path d="M0 1l12 9 12-9" fill="none" stroke="#ffffff" stroke-width="1.6"/></svg>
      info@mapleroster.com
    </p>
    <p class="address">421, Address line, goes here<br>45452,Country Name</p>
  </div>

  <p class="website">www.<span>mapleroster</span>.com</p>
  <div class="accent-bar"></div>
</section>

<section class="card card-back" aria-label="Card back">
  <div class="back-pattern" role="img" aria-label="Faint repeating brand-name pattern across a deep teal background"></div>
  <p class="wordmark">MAPLE ROSTER</p>
</section>

</body>
</html>
```